Business Card Design

We need a business card designed for our new company. Prefer a black card with white logo & writing.

Contact Information for Business Card

Ted Galloway, address: 7-4812 Fernhollow Road, Abbotsford, BC, V3K 8R2, Office Phone: 604-712-3390, Cell: 604-947-2164, Email: ted@resinworkshub.ca

Colors

Designer to choose only greyscale colors for use in the design.

```html
<!DOCTYPE html>
<html lang="en">
<head>
<meta charset="utf-8">
<title>Resinworks Hub – Business Card</title>
<link href="https://fonts.googleapis.com/css2?family=Poppins:wght@400;700;800&display=swap" rel="stylesheet">
<style>
  :root {
    --backdrop: #c9c9c9;
    --card: #050505;
    --ink: #ffffff;
    --ink-soft: #e6e6e6;
  }
  * { margin: 0; padding: 0; box-sizing: border-box; }
  html, body {
    width: 1200px;
    height: 900px;
    overflow: hidden;
    background: var(--backdrop);
    font-family: "Poppins", sans-serif;
  }
  .stage {
    position: relative;
    width: 1200px;
    height: 900px;
  }
  .card {
    position: absolute;
    left: 280px;
    width: 640px;
    height: 366px;
    background: var(--card);
    border-radius: 28px;
    color: var(--ink);
    overflow: hidden;
    box-shadow: 0 10px 24px rgba(0,0,0,0.28);
  }
  .card--front { top: 62px; }
  .card--back  { top: 472px; }

  .wordmark {
    display: flex;
    align-items: center;
    gap: 14px;
    font-weight: 800;
    letter-spacing: 0.5px;
    color: var(--ink);
    text-transform: uppercase;
    line-height: 1;
  }
  .wordmark__square {
    width: 18px;
    height: 18px;
    background: var(--ink);
    flex: none;
  }
  .card--front .wordmark {
    position: absolute;
    left: 50%;
    top: 50%;
    transform: translate(-50%, -50%);
    font-size: 44px;
    white-space: nowrap;
  }
  .card--back .wordmark {
    position: absolute;
    left: 44px;
    top: 118px;
    font-size: 34px;
    white-space: nowrap;
  }

  .holder {
    position: absolute;
    right: 0;
    top: 42px;
    display: flex;
    align-items: center;
    gap: 14px;
  }
  .holder__name {
    font-weight: 700;
    font-size: 21px;
    letter-spacing: 0.6px;
    text-transform: uppercase;
  }
  .holder__tab {
    width: 28px;
    height: 26px;
    background: var(--ink);
  }

  .address {
    position: absolute;
    right: 36px;
    top: 196px;
    text-align: right;
    font-size: 16px;
    line-height: 1.35;
    color: var(--ink-soft);
  }

  .contacts {
    position: absolute;
    left: 44px;
    bottom: 32px;
    list-style: none;
    font-size: 17px;
    line-height: 1.3;
    color: var(--ink-soft);
  }
  .contacts li {
    display: flex;
    align-items: center;
    gap: 10px;
  }
  .contacts svg {
    width: 15px;
    height: 15px;
    flex: none;
  }
</style>
</head>
<body>
<main class="stage">

  <section class="card card--front" aria-label="Card front">
    <div class="wordmark">
      <span class="wordmark__square"></span>
      <span>Resinworks Hub</span>
    </div>
  </section>

  <section class="card card--back" aria-label="Card back">
    <div class="holder">
      <span class="holder__name">Ted Galloway</span>
      <span class="holder__tab"></span>
    </div>

    <div class="wordmark">
      <span class="wordmark__square"></span>
      <span>Resinworks Hub</span>
    </div>

    <address class="address">
      7-4812 Fernhollow Road<br>
      Abbotsford, BC, V3K 8R2
    </address>

    <ul class="contacts">
      <li>
        <svg viewBox="0 0 24 24" fill="none" stroke="currentColor" stroke-width="2" stroke-linecap="round" stroke-linejoin="round" aria-hidden="true">
          <path d="M5 3h4l2 5-2.5 1.5a11 11 0 0 0 6 6L16 13l5 2v4a2 2 0 0 1-2 2A16 16 0 0 1 3 5a2 2 0 0 1 2-2z"/>
        </svg>
        <span>604-712-3390</span>
      </li>
      <li>
        <svg viewBox="0 0 24 24" fill="none" stroke="currentColor" stroke-width="2" stroke-linecap="round" stroke-linejoin="round" aria-hidden="true">
          <rect x="6" y="2" width="12" height="20" rx="2"/>
          <line x1="11" y1="18" x2="13" y2="18"/>
        </svg>
        <span>604-947-2164</span>
      </li>
      <li>
        <svg viewBox="0 0 24 24" fill="none" stroke="currentColor" stroke-width="2" stroke-linecap="round" stroke-linejoin="round" aria-hidden="true">
          <rect x="2" y="5" width="20" height="14" rx="1"/>
          <polyline points="2,6 12,13 22,6"/>
        </svg>
        <span>ted@resinworkshub.ca</span>
      </li>
    </ul>
  </section>

</main>
</body>
</html>
```